Online Banner and skyscrapper ads

Design ads for real estate company in Australia to be used on Nest huntr.com.au details below
sizes
Leaderboard Specifications
• Dimensions: 728×90px
• Format: HTML5 or Animated/Static Gif
• Max file size: 100kb (HTML5), 80kb (GIF, JPG, PNG)
• Back-up image: 40kb (GIF, JPG, PNG). Back-up image only required if you supply an HTML5 banner.
• Looping: Yes
• See Leaderboard for more information.
Email Alert Strip Ad (EASA) Specifications
• Dimensions: 472×114 px
• Format: JPEG, PNG or Static GIF
• File Size: 20kb
• Looping: No
Skyscraper Specifications
• Dimensions: 160x600px
• Looping: Yes
• See Skyscraper for more information.
Mega Skyscraper Specifications
• Dimensions: 300x600px
• Format: HTML5 or Animated/Static GIF
• File size: 100kb (Html5) or 80kb (GIF, JPG, PNG)
• Back-up image: 40kb (JPG or PNG). Back-up image only required if you supply an HTML5 banner.
• Looping: Yes
• See Half Page for more information.

I would like them to be quite simple , TREVANCE Your Faulconbridge property experts and another saying TREVANCE your Lawson property experts and TREVANCE your Hazelbrook property experts (3 different versions all up ) and another version MOIRA DELVINE your Faulconbridge property expert with logo and her image , i've put a photo of the top banner example and a video of the side banner it has a video in the background that i will get produced if it works

```html
<!DOCTYPE html>
<html lang="en">
<head>
<meta charset="UTF-8">
<title>TREVANCE – Your Faulcon Bridge Property Experts</title>
<link rel="stylesheet" href="https://fonts.googleapis.com/css2?family=Montserrat:wght@300;400;500&display=swap">
<style>
  :root {
    --scene-dark: #26302c;
    --scene-mid: #3c4a45;
    --scene-light: #5d6b66;
    --scene-warm: #6f6a5c;
    --brand-cream: #e4e2c4;
    --text-white: #ffffff;
  }
  html, body {
    margin: 0;
    padding: 0;
    width: 1200px;
    height: 2400px;
    overflow: hidden;
    background: var(--scene-dark);
  }
  .skyscraper-ad {
    position: relative;
    width: 1200px;
    height: 2400px;
    overflow: hidden;
    font-family: "Montserrat", sans-serif;
  }
  .background-video-still {
    position: absolute;
    inset: 0;
    background:
      linear-gradient(180deg, rgba(38,48,44,0.2) 0%, rgba(38,48,44,0.55) 55%, rgba(38,48,44,0.35) 100%),
      linear-gradient(115deg, var(--scene-mid) 0%, var(--scene-dark) 35%, var(--scene-light) 70%, var(--scene-warm) 100%);
  }
  .brand-block {
    position: absolute;
    top: 720px;
    left: 0;
    width: 100%;
    text-align: center;
    color: var(--brand-cream);
  }
  .brand-mark {
    display: block;
    width: 64px;
    height: 64px;
    margin: 0 auto 52px;
    border: 8px solid var(--brand-cream);
    box-sizing: border-box;
  }
  .brand-name {
    margin: 0;
    font-size: 112px;
    font-weight: 400;
    letter-spacing: 12px;
    line-height: 1;
  }
  .brand-since {
    margin: 56px 0 0;
    font-size: 42px;
    font-weight: 400;
    letter-spacing: 14px;
    line-height: 1;
  }
  .tagline {
    position: absolute;
    top: 1330px;
    left: 0;
    width: 100%;
    margin: 0;
    text-align: center;
    color: var(--text-white);
    font-weight: 400;
    line-height: 1;
  }
  .tagline span { display: block; }
  .tagline-lead { font-size: 108px; font-weight: 300; }
  .tagline-place { font-size: 110px; font-weight: 500; margin-top: 14px; }
  .tagline-role { font-size: 100px; font-weight: 400; margin-top: 20px; }
</style>
</head>
<body>
  <main class="skyscraper-ad">
    <div class="background-video-still" role="img" aria-label="Background video: a man walking along a timber deck beneath a pergola beside a house, tinted dark green"></div>

    <header class="brand-block">
      <span class="brand-mark" aria-hidden="true"></span>
      <h1 class="brand-name">TREVANCE</h1>
      <p class="brand-since">SINCE 1987</p>
    </header>

    <h2 class="tagline">
      <span class="tagline-lead">Your</span>
      <span class="tagline-place">Faulcon Bridge</span>
      <span class="tagline-role">Property Experts</span>
    </h2>
  </main>
</body>
</html>
```